Mother's Day Sale Banner Ad For Jewelry Site

We are looking for a designer to design a banner on our website advertising our Mother's Day Sale. I have enclosed a few pieces of jewelry we would like used in the ad. The ad size needs to be 1187 × 400. The ad should say:

Mother's Day Sale - Save 15% with Promo Code: LOVEMOM

Jewelry

```html
<!DOCTYPE html>
<html lang="en">
<head>
<meta charset="utf-8">
<title>Mother's Day Sale</title>
<link href="https://fonts.googleapis.com/css2?family=Raleway:wght@500;600&family=Josefin+Sans:wght@400;500&display=swap" rel="stylesheet">
<style>
  :root {
    --bg-left: #fdfcf6;
    --bg-right: #f1e9cd;
    --ink: #2f2b26;
    --gold-light: #f4de86;
    --gold: #d4a21c;
    --gold-deep: #b9870f;
    --ruby: #b0275e;
    --silver: #e6e3dc;
  }
  html, body { margin: 0; padding: 0; overflow: hidden; }
  .banner {
    position: relative;
    width: 1200px;
    height: 404px;
    overflow: hidden;
    background: linear-gradient(90deg, var(--bg-left) 0%, #faf6e8 40%, var(--bg-right) 100%);
    font-family: "Raleway", sans-serif;
    color: var(--ink);
  }
  .sale-tag {
    position: absolute;
    left: 0;
    top: 88px;
    width: 424px;
    height: 32px;
    background: linear-gradient(90deg, rgba(244,222,134,0) 0%, rgba(244,222,134,0.35) 30%, var(--gold-light) 100%);
  }
  .sale-tag span {
    position: absolute;
    left: 97px;
    top: 5px;
    font-size: 20px;
    font-weight: 500;
    letter-spacing: 2px;
    white-space: nowrap;
  }
  .headline {
    position: absolute;
    left: 97px;
    top: 150px;
    margin: 0;
    font-size: 44px;
    font-weight: 500;
    line-height: 1;
  }
  .subline {
    position: absolute;
    left: 97px;
    top: 204px;
    margin: 0;
    font-size: 30px;
    font-weight: 500;
    line-height: 1;
  }
  .promo-code {
    position: absolute;
    left: 94px;
    top: 258px;
    margin: 0;
    font-family: "Josefin Sans", sans-serif;
    font-size: 60px;
    font-weight: 400;
    letter-spacing: 3px;
    line-height: 1;
    background: linear-gradient(180deg, var(--gold-light) 0%, var(--gold) 55%, var(--gold-deep) 100%);
    -webkit-background-clip: text;
    background-clip: text;
    color: transparent;
  }
  .product {
    position: absolute;
  }
  .product-brooch {
    left: 540px; top: 20px; width: 285px; height: 320px;
    border-radius: 45%;
    background: radial-gradient(ellipse at 50% 62%, var(--ruby) 0%, #c9476f 30%, var(--gold) 55%, rgba(241,233,205,0) 72%);
  }
  .product-earrings {
    left: 855px; top: 70px; width: 285px; height: 130px;
    border-radius: 40%;
    background: radial-gradient(ellipse at 50% 50%, var(--gold) 0%, var(--silver) 40%, rgba(241,233,205,0) 70%);
  }
  .product-ring {
    left: 945px; top: 215px; width: 180px; height: 120px;
    border-radius: 40%;
    background: radial-gradient(ellipse at 50% 50%, var(--silver) 0%, var(--gold) 45%, rgba(241,233,205,0) 70%);
  }
</style>
</head>
<body>
<div class="banner">
  <div class="sale-tag"><span>MOTHER'S DAY SALE</span></div>
  <p class="headline">Save 15%</p>
  <p class="subline">with Promo Code:</p>
  <p class="promo-code">LOVEMOM</p>
  <div class="product product-brooch" role="img" aria-label="Gold crab brooch set with pink sapphires and blue sapphire eyes"></div>
  <div class="product product-earrings" role="img" aria-label="Pair of gold rope earrings with diamond X accents"></div>
  <div class="product product-ring" role="img" aria-label="Gold and white gold filigree band ring"></div>
</div>
</body>
</html>
```